Design a website for a newly developed Delta 8 THC Company

Design a responsive Website with the following goals in mind:
- Built on Wordpress/WooCommerce theme. Please use this when designing for ease of integration.
- Build trust with website visitors with an engaging, informative content driven website, that leads to a conversion of product purchase and repeat business. We will also be driving consumers to businesses that carry our products as well.
- The website will embody a lifestyle feel and make the visitor identify with the content.
- The website will allow for super charged SEO and other digital marketing and advertising strategies and tactics used to increase discovery, awareness, and conversion.
Please see additional goals in the uploaded files.
Target Market(s)
Male/Female 21-
Industry/Entity Type
Cannabis/Hemp
Coding
Coded - Design and coding required
Number of Pages Required
5+ page
Font styles to use
Other font styles liked:
- Montserrat
Look and feel
Each slider illustrates characteristics of the customer's brand and the style your logo design should communicate.

```html
<!DOCTYPE html>
<html lang="en">
<head>
<meta charset="utf-8">
<title>Lumora — Delta 8</title>
<link href="https://fonts.googleapis.com/css2?family=Montserrat:wght@400;500;600;700;800&display=swap" rel="stylesheet">
<style>
:root{
  --black:#050505;
  --ink:#111111;
  --gold:#c9973f;
  --gold-light:#e8be6a;
  --gold-dark:#a8772c;
  --white:#ffffff;
  --grey:#6b6b6b;
  --slate:#2e2d30;
}
*{box-sizing:border-box;margin:0;padding:0}
html,body{width:1200px;height:3286px;overflow:hidden}
body{position:relative;font-family:'Montserrat',sans-serif;background:var(--white);color:var(--ink)}
.btn{display:flex;align-items:center;justify-content:center;border-radius:40px;color:var(--white);font-weight:700;text-transform:uppercase;background:linear-gradient(180deg,var(--gold-light),var(--gold-dark));}

/* header */
.site-header{position:absolute;left:0;top:0;width:1200px;height:110px;background:var(--black);border-bottom:3px solid var(--gold);z-index:3}
.main-nav{position:absolute;left:140px;top:52px;display:flex;gap:25px;font-size:12px;font-weight:600;color:var(--white)}
.main-nav .active{border-bottom:2px solid var(--gold);padding-bottom:8px}
.search{position:absolute;left:748px;top:40px;width:234px;height:37px;border:1px solid #3a3a3a;color:#ccc;font-size:11px;padding:12px 20px}
.search svg{position:absolute;right:14px;top:11px}
.cart{position:absolute;left:1008px;top:44px}
.cart-badge{position:absolute;left:1035px;top:34px;width:20px;height:20px;border-radius:50%;background:var(--gold);color:var(--ink);font-size:10px;font-weight:700;display:flex;align-items:center;justify-content:center}
.brand-tab{position:absolute;left:497px;top:107px;width:207px;height:88px;border-radius:0 0 104px 104px/0 0 88px 88px;background:var(--black);border:3px solid var(--gold);border-top:none;z-index:4}
.brand-head{position:absolute;left:497px;top:0;width:207px;height:196px;z-index:5;display:flex;flex-direction:column;align-items:center;padding-top:62px;gap:44px}
.brand-mark{width:18px;height:18px;border-radius:50%;background:var(--gold)}
.brand-name{font-size:22px;font-weight:500;letter-spacing:9px;color:var(--gold);padding-left:9px}

/* hero */
.hero{position:absolute;left:0;top:110px;width:1200px;height:606px;
  background:
    radial-gradient(ellipse 160px 120px at 90px 80px,rgba(226,176,40,.85),transparent 70%),
    radial-gradient(ellipse 180px 130px at 330px 60px,rgba(196,30,30,.8),transparent 70%),
    radial-gradient(ellipse 150px 150px at 320px 230px,rgba(225,200,170,.6),transparent 70%),
    radial-gradient(ellipse 160px 120px at 130px 260px,rgba(240,190,40,.8),transparent 70%),
    radial-gradient(ellipse 190px 150px at 420px 360px,rgba(110,120,60,.55),transparent 70%),
    radial-gradient(ellipse 200px 150px at 150px 500px,rgba(190,25,30,.8),transparent 70%),
    radial-gradient(ellipse 150px 130px at 390px 560px,rgba(230,160,30,.8),transparent 70%),
    radial-gradient(ellipse 120px 120px at 560px 70px,rgba(220,175,40,.6),transparent 70%),
    linear-gradient(90deg,#3b3530 0%,#333032 45%,var(--slate) 60%,#302f33 100%)}
.hero-title{position:absolute;left:646px;top:160px;font-size:92px;font-weight:800;color:var(--gold-light);letter-spacing:2px;line-height:1}
.hero-text{position:absolute;left:648px;top:276px;width:420px;font-size:19px;font-weight:600;color:var(--white);line-height:31px}
.hero .btn{position:absolute;left:650px;top:375px;width:184px;height:58px;font-size:19px}
.dots{position:absolute;left:648px;top:531px;display:flex;gap:10px}
.dots span{width:9px;height:9px;border-radius:50%;background:var(--white)}
.dots .on{background:var(--gold)}

/* products */
.section-title{position:absolute;left:0;width:1200px;text-align:center;font-size:32px;font-weight:700;color:var(--ink)}
.product{position:absolute;width:220px;text-align:center}
.product-img{width:220px;height:150px;box-shadow:0 0 8px rgba(0,0,0,.14)}
.product-name{margin-top:25px;font-size:12px;font-weight:500}
.product-price{margin-top:10px;font-size:11px;color:var(--gold)}
.stars{margin-top:10px;height:10px}
.product .btn{margin:18px auto 0;width:98px;height:32px;font-size:10px}

/* categories */
.category{position:absolute;top:1587px;width:596px;height:354px}
.category h2{position:absolute;left:143px;top:100px;font-size:38px;font-weight:700;color:var(--white);line-height:46px}
.category .btn{position:absolute;left:143px;top:209px;width:127px;height:40px;font-size:13px}

/* newsletter */
.news-text{position:absolute;left:0;top:2108px;width:1200px;text-align:center;font-size:14px;color:var(--grey)}
.news-form{position:absolute;left:333px;top:2175px;width:533px;height:50px;border:1px solid #c9c9c9;border-radius:30px;font-size:11px;padding:18px 30px}
.news-form .btn{position:absolute;right:-1px;top:-1px;width:125px;height:50px;font-size:13px}

/* gallery */
.gallery{position:absolute;left:0;top:2312px;width:1200px;height:536px;display:grid;grid-template-columns:repeat(4,1fr);grid-template-rows:repeat(2,1fr);gap:2px;background:#fff}

/* footer */
.site-footer{position:absolute;left:0;top:2848px;width:1200px;height:438px;background:var(--black);color:var(--white);text-align:center}
.footer-brand{position:absolute;left:0;top:150px;width:1200px;display:flex;justify-content:center;align-items:center;gap:14px}
.footer-nav{position:absolute;left:0;top:226px;width:1200px;display:flex;justify-content:center;gap:38px;font-size:17px;font-weight:700}
.copyright{position:absolute;left:0;top:278px;width:1200px;font-size:11px}
.social{position:absolute;left:562px;top:328px;display:flex;gap:20px}
.social span{width:28px;height:28px;border-radius:5px;background:var(--white)}
.payments{position:absolute;left:504px;top:387px;display:flex;gap:8px}
.payments span{width:32px;height:22px;border-radius:3px;background:#d9d9d9}
</style>
</head>
<body>

<header class="site-header">
  <nav class="main-nav">
    <span class="active">HOME</span><span>ABOUT</span><span>SHOP</span><span>NEWS</span><span>CONTACT US</span>
  </nav>
  <div class="search">Search
    <svg width="12" height="12" viewBox="0 0 12 12"><circle cx="5" cy="5" r="3.8" fill="none" stroke="#fff" stroke-width="1.8"/><line x1="8" y1="8" x2="11" y2="11" stroke="#fff" stroke-width="2"/></svg>
  </div>
  <svg class="cart" width="32" height="28" viewBox="0 0 32 28"><path d="M0 2h6l4 16h17l4-12H9" fill="none" stroke="#fff" stroke-width="3"/><path d="M9 6h22l-4 12H12z" fill="#fff"/><circle cx="13" cy="24" r="3" fill="#fff"/><circle cx="25" cy="24" r="3" fill="#fff"/></svg>
  <div class="cart-badge">0</div>
</header>
<div class="brand-tab"></div>
<div class="brand-head"><span class="brand-mark"></span><span class="brand-name">LUMORA</span></div>

<section class="hero" role="img" aria-label="Red, yellow and clear gummy bears with cannabis buds on dark slate">
  <h1 class="hero-title">DELTA 8</h1>
  <p class="hero-text">Lorem ipsum dolor sit amet consectetur adipiscing elitam libero tempor</p>
  <a class="btn">Shop Now</a>
  <div class="dots"><span></span><span></span><span class="on"></span><span></span><span></span></div>
</section>

<h2 class="section-title" style="top:787px">FEATURED PRODUCTS</h2>

<div class="product" style="left:140px;top:869px"><div class="product-img" role="img" aria-label="Green gummies in a glass bowl with buds" style="background:radial-gradient(ellipse 70px 40px at 50% 50%,rgba(90,200,60,.55),transparent 70%),radial-gradient(ellipse 100px 45px at 50% 52%,rgba(120,100,50,.45),transparent 75%),#fff"></div><p class="product-name">PRODUCT NAME</p><p class="product-price">$56.76</p><svg class="stars" width="52" height="10"><text x="0" y="9" font-size="10" fill="#111">★★★★★</text></svg><a class="btn">Shop Now</a></div>
<div class="product" style="left:374px;top:869px"><div class="product-img" role="img" aria-label="Vape pen and cartridges" style="background:radial-gradient(ellipse 30px 50px at 35% 48%,rgba(30,30,30,.35),transparent 75%),radial-gradient(ellipse 45px 30px at 68% 50%,rgba(200,160,60,.45),transparent 75%),#fff"></div><p class="product-name">PRODUCT NAME</p><p class="product-price">$56.76</p><svg class="stars" width="52" height="10"><text x="0" y="9" font-size="10" fill="#111">★★★★★</text></svg><a class="btn">Shop Now</a></div>
<div class="product" style="left:606px;top:869px"><div class="product-img" role="img" aria-label="Stacks of orange, red and green gummies" style="background:radial-gradient(ellipse 25px 25px at 22% 55%,rgba(245,110,30,.7),transparent 75%),radial-gradient(ellipse 25px 25px at 42% 55%,rgba(225,40,40,.7),transparent 75%),radial-gradient(ellipse 25px 25px at 62% 55%,rgba(200,30,40,.7),transparent 75%),radial-gradient(ellipse 25px 25px at 80% 52%,rgba(100,120,50,.6),transparent 75%),#fff"></div><p class="product-name">PRODUCT NAME</p><p class="product-price">$56.76</p><svg class="stars" width="52" height="10"><text x="0" y="9" font-size="10" fill="#111">★★★★★</text></svg><a class="btn">Shop Now</a></div>
<div class="product" style="left:839px;top:869px"><div class="product-img" role="img" aria-label="Tincture bottle with gummies" style="background:radial-gradient(ellipse 25px 55px at 72% 42%,rgba(20,20,20,.6),transparent 75%),radial-gradient(ellipse 40px 20px at 40% 82%,rgba(200,60,160,.45),transparent 75%),#fff"></div><p class="product-name">PRODUCT NAME</p><p class="product-price">$56.76</p><svg class="stars" width="52" height="10"><text x="0" y="9" font-size="10" fill="#111">★★★★★</text></svg><a class="btn">Shop Now</a></div>

<div class="product" style="left:140px;top:1197px"><div class="product-img" role="img" aria-label="Tincture bottle with colourful gummies" style="background:radial-gradient(ellipse 25px 55px at 68% 45%,rgba(20,20,20,.6),transparent 75%),radial-gradient(ellipse 45px 20px at 35% 75%,rgba(80,190,180,.45),transparent 75%),#fff"></div><p class="product-name">PRODUCT NAME</p><p class="product-price">$56.76</p><svg class="stars" width="52" height="10"><text x="0" y="9" font-size="10" fill="#111">★★★★★</text></svg><a class="btn">Shop Now</a></div>
<div class="product" style="left:374px;top:1197px"><div class="product-img" role="img" aria-label="Four coloured vape devices" style="background:radial-gradient(ellipse 10px 45px at 18% 50%,rgba(20,20,20,.5),transparent 80%),radial-gradient(ellipse 10px 45px at 39% 50%,rgba(200,20,20,.5),transparent 80%),radial-gradient(ellipse 10px 45px at 61% 50%,rgba(20,40,200,.5),transparent 80%),radial-gradient(ellipse 10px 45px at 82% 50%,rgba(230,150,30,.55),transparent 80%),#fff"></div><p class="product-name">PRODUCT NAME</p><p class="product-price">$56.76</p><svg class="stars" width="52" height="10"><text x="0" y="9" font-size="10" fill="#111">★★★★★</text></svg><a class="btn">Shop Now</a></div>
<div class="product" style="left:606px;top:1197px"><div class="product-img" role="img" aria-label="Pouch of gummies" style="background:radial-gradient(ellipse 45px 60px at 52% 50%,rgba(60,50,60,.55),transparent 75%),radial-gradient(ellipse 30px 30px at 48% 40%,rgba(220,60,60,.45),transparent 75%),#fff"></div><p class="product-name">PRODUCT NAME</p><p class="product-price">$56.76</p><svg class="stars" width="52" height="10"><text x="0" y="9" font-size="10" fill="#111">★★★★★</text></svg><a class="btn">Shop Now</a></div>
<div class="product" style="left:839px;top:1197px"><div class="product-img" role="img" aria-label="Oil bottle, vape pen and buds" style="background:radial-gradient(ellipse 30px 45px at 55% 50%,rgba(120,70,20,.55),transparent 75%),radial-gradient(ellipse 80px 18px at 50% 80%,rgba(120,120,120,.4),transparent 75%),#fff"></div><p class="product-name">PRODUCT NAME</p><p class="product-price">$56.76</p><svg class="stars" width="52" height="10"><text x="0" y="9" font-size="10" fill="#111">★★★★★</text></svg><a class="btn">Shop Now</a></div>

<section class="category" style="left:0;background:radial-gradient(ellipse 90px 60px at 220px 60px,rgba(230,150,170,.7),transparent 70%),radial-gradient(ellipse 160px 110px at 440px 110px,rgba(240,170,110,.6),transparent 70%),radial-gradient(ellipse 80px 60px at 500px 250px,rgba(110,200,90,.55),transparent 70%),radial-gradient(ellipse 90px 60px at 40px 80px,rgba(90,170,80,.5),transparent 70%),radial-gradient(ellipse 200px 100px at 200px 310px,rgba(60,70,40,.7),transparent 70%),linear-gradient(120deg,#5d5048,#6f625a 45%,#4a4038)" role="img" aria-label="Colourful gummy bears in a bowl with buds on wood">
  <h2>CANNABIS<br>GUMMIES</h2><a class="btn">Shop Now</a>
</section>
<section class="category" style="left:604px;background:radial-gradient(ellipse 140px 90px at 480px 60px,rgba(110,120,80,.6),transparent 70%),radial-gradient(ellipse 150px 90px at 80px 90px,rgba(90,100,70,.5),transparent 70%),radial-gradient(ellipse 200px 60px at 420px 290px,rgba(200,150,60,.6),transparent 70%),linear-gradient(120deg,#3a3d36,#2c2d33 50%,#302c28)" role="img" aria-label="Vape cartridge beside cannabis buds on dark stone">
  <h2 style="left:85px">CANNABIS<br>VAPE</h2><a class="btn" style="left:85px">Shop Now</a>
</section>

<h2 class="section-title" style="top:2033px">SIGN UP OUR NEWSLETTER</h2>
<p class="news-text">At vero eos et accusamus et iusto os ducimus qui blanditiis praesentium</p>
<div class="news-form">Enter Email<a class="btn">Sign Up</a></div>

<section class="gallery">
  <div role="img" aria-label="Jar of amber oil on blue wood" style="background:radial-gradient(ellipse 70px 90px at 45% 55%,rgba(220,140,30,.85),transparent 72%),linear-gradient(160deg,#3a2e24 0%,#2a3e5c 55%,#1e3a6a 100%)"></div>
  <div role="img" aria-label="Black gummy package" style="background:radial-gradient(ellipse 60px 60px at 50% 35%,rgba(201,151,63,.35),transparent 70%),#0f0f0f"></div>
  <div role="img" aria-label="Close-up of red and yellow gummy worms" style="background:radial-gradient(ellipse 120px 80px at 30% 30%,rgba(230,160,30,.8),transparent 70%),radial-gradient(ellipse 120px 90px at 70% 75%,rgba(120,90,40,.7),transparent 70%),linear-gradient(135deg,#c8341e,#d8601e 60%,#e0a020)"></div>
  <div role="img" aria-label="Colourful gummies and buds on dark surface" style="background:radial-gradient(ellipse 60px 50px at 30% 20%,rgba(120,220,110,.7),transparent 70%),radial-gradient(ellipse 60px 50px at 80% 45%,rgba(230,130,170,.7),transparent 70%),radial-gradient(ellipse 60px 50px at 60% 80%,rgba(240,200,80,.7),transparent 70%),linear-gradient(135deg,#2e3230,#3e4a38)"></div>
  <div role="img" aria-label="Black vape packaging" style="background:radial-gradient(ellipse 80px 80px at 50% 40%,rgba(201,151,63,.35),transparent 70%),#0d0d0d"></div>
  <div role="img" aria-label="Hand holding a vape pen among leaves" style="background:radial-gradient(ellipse 70px 60px at 50% 70%,rgba(220,190,170,.55),transparent 70%),linear-gradient(135deg,#2d3a2a,#4a5a44)"></div>
  <div role="img" aria-label="Black gummy package" style="background:radial-gradient(ellipse 60px 60px at 50% 35%,rgba(201,151,63,.35),transparent 70%),#111"></div>
  <div role="img" aria-label="Jar with watermelon gummies" style="background:radial-gradient(ellipse 60px 80px at 40% 70%,rgba(20,20,30,.85),transparent 72%),radial-gradient(ellipse 110px 70px at 65% 25%,rgba(230,110,100,.7),transparent 70%),linear-gradient(135deg,#f2ece8,#e8d8d2)"></div>
</section>

<footer class="site-footer">
  <div class="footer-brand"><span class="brand-mark"></span><span class="brand-name">LUMORA</span></div>
  <nav class="footer-nav"><span>HOME</span><span>ABOUT</span><span>SHOP</span><span>NEWS</span><span>CONTACT US</span></nav>
  <p class="copyright">© 2021 Lumora. All rights reserved.Privacy Terms of Use</p>
  <div class="social"><span></span><span></span></div>
  <div class="payments"><span></span><span></span><span></span><span></span><span></span></div>
</footer>

</body>
</html>
```